Website improvements and Adding Functionalities at https://mervo.site/tarnovex

1.Search functionality
2.Payment process functionality
3. Application configuration
4. Registration functionality activation
5. Chat functionality
6.Language switching functionality (Portuguese & French)
7.Bespoke interactive modules
8. Automated web scraping and data synchronisation mechanisms
9. News Page
10.Webinar facilities
11. Basic SEO optimisation
12. Speed and performance optimisation
13. Security configuration
14. Google Analytics integration
15. Cross-browser and mobile testing
16. Website deployment and launch support

Target Market(s)

My target markets are companies, investors, suppliers and professionals with an interest in the Mozambican oil and gas sector

Industry/Entity Type

Oil and Gas

Coding

Coded - Design and coding required

Number of Pages Required

1 page

Requirements
Must have
• Improve the existing page at https://mervo.site/tarnovex and add the following features to it: 1. Search functionality 2. Payment process functionality 3. Application configuration 4. Activation of registration functionality 5. Chat functionality 6. Language switching functionality (Portuguese & French) 7. Bespoke interactive modules 8. Automated web scraping and data synchronisation mechanisms 9. News Page

```html
<!DOCTYPE html>
<html lang="en">
<head>
<meta charset="utf-8">
<title>Tarnovex — Mozambique Energy Platform</title>
<link href="https://fonts.googleapis.com/css2?family=Outfit:wght@400;500;600&family=Inter:wght@400;500;600&family=JetBrains+Mono:wght@500;800&display=swap" rel="stylesheet">
<style>
:root{
  --navy:#0f1b2d;
  --navy-deep:#0b1524;
  --panel:#15233a;
  --panel-2:#1a2b45;
  --line:#26374f;
  --gold:#e4b53f;
  --gold-soft:#c99a2c;
  --text:#f3f5f8;
  --muted:#9aa7b8;
  --dim:#6c7a8d;
  --green:#2ed47a;
  --black:#05080d;
}
*{box-sizing:border-box;margin:0;padding:0}
html,body{width:1066px;height:1200px;overflow:hidden;background:#fff}
body{font-family:Inter,sans-serif;color:var(--text)}
.stage{position:absolute;left:0;top:0;width:1816px;height:2044px;transform:scale(0.587);transform-origin:0 0;overflow:hidden;background:#fff}
.abs{position:absolute}
.head{font-family:Outfit,sans-serif;font-weight:500;letter-spacing:-0.02em;line-height:1.05}
.mono{font-family:"JetBrains Mono",monospace}
.label{font-size:8px;letter-spacing:.12em;color:var(--gold);text-transform:uppercase;font-weight:500}
.pill{position:absolute;border:1px solid var(--line);border-radius:20px;display:flex;align-items:center;justify-content:center;font-size:9px;font-weight:500;white-space:nowrap}
.ph{position:absolute}

.col-left{position:absolute;left:0;top:0;width:908px;height:1546px;background:var(--navy)}
.col-right{position:absolute;left:908px;top:0;width:908px;height:2044px;background:var(--navy-deep)}

.nav{position:absolute;left:0;top:0;width:908px;height:48px;background:#0a121e}
.brand{position:absolute;left:14px;top:12px;font-family:"JetBrains Mono",monospace;font-weight:800;font-size:20px;letter-spacing:.08em}
.nav-links{position:absolute;left:163px;top:19px;display:flex;gap:21px;font-size:9px;font-weight:600}
.btn-gold{background:var(--gold);color:#14110a;border-radius:8px;display:flex;align-items:center;justify-content:center;gap:6px;font-weight:600;white-space:nowrap}

.hero-bg{position:absolute;left:0;top:48px;width:908px;height:460px;background:linear-gradient(90deg,rgba(12,22,38,.92) 0%,rgba(22,36,56,.7) 45%,rgba(40,44,50,.55) 65%,rgba(12,22,38,.9) 100%),linear-gradient(180deg,#7a6a52 0%,#3a3a3c 40%,#14202f 100%)}
.hero h1{position:absolute;left:24px;top:125px;width:520px;font-size:54px}
.search{position:absolute;left:24px;top:320px;width:402px;height:48px;border:1px solid #3a4a60;border-radius:12px;background:rgba(20,32,50,.7)}
.tag{position:absolute;top:378px;height:14px;border:1px solid #3a4a60;border-radius:8px;font-size:7px;display:flex;align-items:center;padding:0 11px;color:#d6dce4;white-space:nowrap}

.fcard{position:absolute;top:738px;width:204px;height:230px;background:var(--panel);border:1px solid var(--line);border-radius:12px;padding:24px 12px 24px 24px}
.ficon{width:33px;height:33px;border-radius:8px;background:#22324b;display:flex;align-items:center;justify-content:center;margin-bottom:32px}
.fcard h3{font-size:18px;letter-spacing:-0.03em;margin-bottom:14px}
.fcard p{font-size:9px;line-height:1.6;color:var(--muted);padding-right:12px}

.step{position:absolute;left:398px;width:486px;height:82px;background:var(--panel);border:1px solid var(--line);border-radius:12px}
.step .num{position:absolute;left:20px;top:20px;width:28px;height:28px;border-radius:6px;background:#283850;font-family:"JetBrains Mono",monospace;font-size:10px;color:var(--gold);display:flex;align-items:center;justify-content:center}
.step h4{position:absolute;left:68px;top:22px;font-size:15px;white-space:nowrap}
.step p{position:absolute;left:68px;top:50px;font-size:9px;color:var(--muted);white-space:nowrap}

.dash{position:absolute;left:24px;top:147px;width:858px;height:689px;border:1px solid var(--line);border-radius:14px;background:#0d1828}
.stat{position:absolute;top:52px;height:133px;background:#0a0f17;border:1px solid var(--line);border-radius:12px;padding:18px}
.stat .k{font-size:7px;letter-spacing:.12em;color:var(--dim)}
.inner{position:absolute;left:20px;top:207px;width:818px;height:462px;background:#14223a;border-radius:10px;overflow:hidden}
.side{position:absolute;left:0;top:0;width:127px;height:462px;background:#111d31}
.side-item{position:absolute;left:14px;font-size:8px;color:#d6dce4;display:flex;gap:6px;align-items:center;white-space:nowrap}
.side-item i{width:9px;height:9px;border:1px solid #c9d1dc;border-radius:3px;display:inline-block}
.chart{position:absolute;background:#1b2c47;border-radius:6px;padding:8px}
.chart .t{font-size:8px;color:#e6ebf1}

.ncard{position:absolute;top:1045px;width:276px;height:295px;background:var(--panel-2);border-radius:12px;overflow:hidden}
.ncard .img{position:absolute;left:0;top:0;width:100%;height:143px}
.ncard .ago{position:absolute;right:12px;top:12px;background:#111;border-radius:8px;padding:3px 8px;font-size:7px}
.ncard .cat{position:absolute;left:20px;top:163px;font-size:6px;letter-spacing:.1em;color:var(--gold)}
.ncard h5{position:absolute;left:20px;top:179px;width:240px;font-size:12px;font-weight:600;line-height:1.25}
.ncard p{position:absolute;left:20px;top:224px;width:236px;font-size:8px;line-height:1.45;color:var(--muted)}
.ncard .meta{position:absolute;left:20px;right:20px;top:265px;display:flex;justify-content:space-between;font-size:7px}

.fcol{position:absolute;top:1828px;font-size:8px;line-height:2.75;color:#c7d0dc;white-space:nowrap}
.fcol b{display:block;font-size:7px;letter-spacing:.15em;color:var(--gold);font-weight:500;line-height:1;margin-bottom:14px}
</style>
</head>
<body>
<div class="stage">

<section class="col-left">
  <header class="nav">
    <div class="brand">TARNOVEX</div>
    <nav class="nav-links"><span>PLATFORM</span><span>ANALYTICS</span><span>MARKETPLACE</span><span>INSIGHTS</span></nav>
    <div class="pill" style="left:563px;top:12px;width:57px;height:24px;color:#dfe4ea;background:#111b2a">EN ›</div>
    <div class="pill" style="left:633px;top:12px;width:57px;height:24px;border-color:#55637a">LOG IN</div>
    <div class="abs btn-gold" style="left:705px;top:11px;width:107px;height:26px;font-size:9px">GET STARTED →</div>
    <div class="pill mono" style="left:826px;top:16px;width:57px;height:16px;font-size:6px;color:var(--green);border-color:#1f4a36"><span style="width:5px;height:5px;border-radius:50%;background:var(--green);margin-right:4px"></span>SYNC LIVE</div>
  </header>

  <div class="hero-bg" role="img" aria-label="Offshore drilling rigs at sunset over the sea"></div>
  <div class="hero">
    <div class="pill" style="left:24px;top:87px;width:147px;height:19px;font-size:8px;background:rgba(40,48,60,.7);border-color:#55637a"><span style="width:5px;height:5px;border-radius:50%;background:var(--gold);margin-right:5px"></span>MOZAMBIQUE • EAST AFRICA</div>
    <h1 class="head">Unlock Mozambique's Energy Future</h1>
    <p class="abs" style="left:24px;top:247px;width:320px;font-size:12px;line-height:1.4;color:#dfe4ea">The premier digital platform connecting professionals, investors, and suppliers in Mozambique's thriving oil &amp; gas sector.</p>
    <div class="search">
      <svg class="abs" style="left:18px;top:16px" width="14" height="14" viewBox="0 0 14 14"><circle cx="6" cy="6" r="4.5" fill="none" stroke="#e4b53f" stroke-width="1.4"/><line x1="9.5" y1="9.5" x2="13" y2="13" stroke="#e4b53f" stroke-width="1.4"/></svg>
      <span class="abs" style="left:48px;top:17px;font-size:10px;color:#7d8a9b;white-space:nowrap">Search opportunities, projects, or suppliers...</span>
      <div class="abs btn-gold" style="left:297px;top:6px;width:97px;height:34px;font-size:9px">SEARCH ›</div>
    </div>
    <div class="tag" style="left:24px">Rovuma Basin</div>
    <div class="tag" style="left:100px">Exploration Licenses</div>
    <div class="tag" style="left:196px">Investment Opportunities</div>
    <div class="tag" style="left:310px">Technical Roles</div>

    <div class="ph" style="left:553px;top:205px;width:326px;height:183px;border-radius:14px;background:linear-gradient(120deg,#3d4a5c,#8a7458 50%,#d9b58a 80%,#9fb4c6)" role="img" aria-label="Professionals meeting in a boardroom overlooking offshore platforms"></div>
    <div class="pill" style="left:535px;top:365px;width:196px;height:30px;background:#14203a;border-color:#33435c;font-size:8px;color:var(--gold)"><span class="mono" style="background:#1b3b2f;color:var(--green);padding:2px 6px;border-radius:6px;margin-right:10px;font-size:6px">LIVE</span>142 professionals online in Maputo</div>

    <div class="abs" style="left:24px;top:422px;width:103px;height:38px;background:#fff;color:#111;border-radius:10px;font-size:10px;font-weight:600;display:flex;align-items:center;justify-content:center;white-space:nowrap">Join the Platform →</div>
    <div class="abs" style="left:139px;top:422px;width:84px;height:38px;border:1px solid #55637a;border-radius:10px;font-size:9px;font-weight:600;display:flex;align-items:center;justify-content:center;gap:6px;white-space:nowrap">▷ Watch Demo</div>
    <div class="abs mono" style="left:454px;top:434px;font-size:6px;letter-spacing:.15em;color:#a5b1bf;white-space:nowrap">SCROLL TO EXPLORE</div>
    <div class="abs" style="left:492px;top:452px;width:1px;height:28px;background:#7d8a9b"></div>
    <div class="pill mono" style="left:740px;top:467px;width:148px;height:19px;font-size:6px;background:#0e1826;border-color:#33435c">● ROVUMA BASIN &nbsp;|&nbsp; <span style="color:var(--gold)">&nbsp;BRENT: 81.42</span></div>
    <div class="abs" style="left:24px;top:498px;font-size:7px;color:#8a97a8;display:flex;gap:18px;align-items:center;white-space:nowrap">TRUSTED BY
      <span style="width:26px;height:6px;background:#5a6779;border-radius:2px"></span>
      <span style="width:16px;height:6px;background:#5a6779;border-radius:2px"></span>
      <span style="width:26px;height:6px;background:#5a6779;border-radius:2px"></span>
      <span style="width:32px;height:6px;background:#5a6779;border-radius:2px"></span>
    </div>
  </div>

  <div class="abs label" style="left:0;width:908px;top:575px;text-align:center">WORLD CLASS INFRASTRUCTURE</div>
  <h2 class="abs head" style="left:0;width:908px;top:592px;text-align:center;font-size:37px;line-height:1.0">Enterprise-Grade<br>Energy<br>Intelligence</h2>
  <div class="fcard" style="left:24px"><div class="ficon"><svg width="13" height="13" viewBox="0 0 14 14"><circle cx="7" cy="7" r="6" fill="none" stroke="#e4b53f"/><ellipse cx="7" cy="7" rx="2.5" ry="6" fill="none" stroke="#e4b53f"/><line x1="1" y1="7" x2="13" y2="7" stroke="#e4b53f"/></svg></div><h3 class="head">National Energy<br>Map</h3><p>Real-time geospatial intelligence across all basins with 3D terrain overlays.</p></div>
  <div class="fcard" style="left:243px"><div class="ficon"><svg width="13" height="13" viewBox="0 0 14 14"><polyline points="1,11 5,7 8,9 13,3" fill="none" stroke="#e4b53f"/></svg></div><h3 class="head">Investment<br>Intelligence</h3><p>Track 180+ active projects, ROI forecasts and competitive intelligence.</p></div>
  <div class="fcard" style="left:461px"><div class="ficon"><svg width="13" height="13" viewBox="0 0 14 14"><circle cx="5" cy="5" r="2.5" fill="none" stroke="#e4b53f"/><circle cx="10" cy="5" r="2" fill="none" stroke="#e4b53f"/><path d="M1 12c0-3 8-3 8 0M9 9c2 0 4 1 4 3" fill="none" stroke="#e4b53f"/></svg></div><h3 class="head" style="white-space:nowrap">Talent Marketplace</h3><p>Verified Mozambican professionals and international talent pool.</p></div>
  <div class="fcard" style="left:680px"><div class="ficon"><svg width="13" height="13" viewBox="0 0 14 14"><path d="M2 1v12h11M5 10V6M8 10V4M11 10V7" fill="none" stroke="#e4b53f"/></svg></div><h3 class="head" style="white-space:nowrap">Advanced Analytics</h3><p>Custom dashboards, predictive modeling and automated reporting.</p></div>

  <div class="abs" style="left:0;top:1036px;width:908px;height:1px;background:var(--line)"></div>
  <div class="abs label" style="left:24px;top:1187px">SEAMLESS ONBOARDING</div>
  <h2 class="abs head" style="left:24px;top:1207px;width:360px;font-size:37px">From Registration to Activation in Minutes</h2>
  <p class="abs" style="left:24px;top:1298px;width:230px;font-size:9px;line-height:1.6;color:#c7d0dc">Our platform has been designed specifically for the unique regulatory environment and business culture of Mozambique.</p>
  <div class="abs" style="left:24px;top:1364px;width:141px;height:32px;border:1px solid #7d8a9b;border-radius:8px;font-size:8px;font-weight:500;display:flex;align-items:center;justify-content:center;white-space:nowrap">BEGIN YOUR JOURNEY &nbsp;›</div>
  <div class="step" style="top:1104px;border-color:var(--gold-soft);background:#111c2d"><div class="num">01</div><h4 class="head">Create Profile <span style="color:var(--gold);font-size:10px">⚇</span></h4><p>Register as Professional, Investor or Supplier. Instant verification via BI &amp; NUIT.</p></div>
  <div class="step" style="top:1201px"><div class="num">02</div><h4 class="head">Complete KYC <span style="color:var(--gold);font-size:11px">✓</span></h4><p>Secure document upload with blockchain verification. Takes under 90 seconds.</p></div>
  <div class="step" style="top:1298px"><div class="num">03</div><h4 class="head">Choose Membership <span style="color:var(--gold);font-size:11px">$</span></h4><p>Select from Professional, Enterprise or Institutional tiers with flexible billing.</p></div>
  <div class="step" style="top:1395px"><div class="num">04</div><h4 class="head">Instant Activation <span style="color:var(--gold);font-size:11px">ϟ</span></h4><p>Full platform access with personalized dashboards and live market data.</p></div>
</section>

<section class="col-right">
  <div class="abs label" style="left:24px;top:67px;font-size:7px">POWERFUL INSIGHTS ENGINE</div>
  <h2 class="abs head" style="left:24px;top:82px;font-size:37px;white-space:nowrap">Live Platform Analytics</h2>
  <div class="abs" style="left:636px;top:85px;width:246px;height:32px;border:1px solid var(--line);border-radius:10px;font-size:8px;font-weight:500">
    <div class="abs" style="left:3px;top:3px;width:78px;height:24px;background:#fff;color:#111;border-radius:7px;display:flex;align-items:center;justify-content:center">ANALYTICS</div>
    <span class="abs" style="left:101px;top:11px">BASIN MAP</span><span class="abs" style="left:182px;top:11px">PORTFOLIO</span>
  </div>

  <div class="dash">
    <div class="abs" style="left:40px;top:11px;font-size:8px;color:var(--gold);font-weight:600">DASHBOARD</div>
    <div class="abs mono" style="left:132px;top:11px;font-size:6px;color:var(--green);white-space:nowrap">● ALL SYSTEMS OPERATIONAL</div>
    <div class="abs" style="left:600px;top:11px;font-size:7px;color:#c7d0dc;white-space:nowrap">⌖ CABO DELGADO &nbsp;&nbsp;&nbsp; <b style="color:#fff">Q3 2025 FORECAST</b></div>
    <div class="abs" style="left:768px;top:7px;width:72px;height:16px;background:#1f2b3d;border-radius:8px;font-size:7px;font-weight:600;display:flex;align-items:center;justify-content:center">EXPORT MODE</div>
    <div class="abs" style="left:0;top:32px;width:858px;height:1px;background:var(--line)"></div>

    <div class="stat" style="left:20px;width:332px">
      <div class="k">PRODUCTION YIELD YTD</div>
      <div class="abs head" style="left:18px;top:52px;font-size:26px">92<span style="color:#556">k</span></div>
      <div class="abs head" style="left:18px;top:76px;font-size:13px;color:var(--gold)">BARRELS / DAY</div>
      <div class="abs" style="left:18px;top:92px;width:294px;height:3px;background:#2a3444;border-radius:2px"><div style="width:83%;height:3px;background:var(--gold);border-radius:2px"></div></div>
      <div class="abs" style="left:18px;top:106px;font-size:6px;color:var(--dim)">TARGET 220K</div>
      <div class="abs" style="right:18px;top:106px;font-size:6px;color:var(--green)">+19.4% THIS MONTH</div>
    </div>
    <div class="stat" style="left:366px;width:230px;height:111px">
      <div class="k">ACTIVE PROJECTS</div>
      <div class="abs head" style="left:18px;top:30px;font-size:36px">27</div>
      <svg class="abs" style="right:18px;top:22px" width="22" height="12" viewBox="0 0 22 12"><polyline points="1,11 8,5 12,8 21,1" fill="none" stroke="#2ed47a" stroke-width="1.6"/><polyline points="15,1 21,1 21,6" fill="none" stroke="#2ed47a" stroke-width="1.6"/></svg>
      <div class="abs" style="left:18px;top:85px;font-size:6px;color:var(--muted);white-space:nowrap">4 new this month • 2 awaiting FID</div>
    </div>
    <div class="stat" style="left:610px;width:229px;height:111px;overflow:hidden">
      <div class="k">INVESTMENT PIPELINE</div>
      <div class="abs head" style="left:18px;top:36px;font-size:24px">$2.8B</div>
      <div class="abs" style="left:18px;top:66px;font-size:7px;color:var(--gold)">↑ 41% from last quarter</div>
      <div class="abs head" style="right:-4px;top:40px;font-size:70px;color:#1a212c">28</div>
    </div>

    <div class="inner">
      <div class="side">
        <div class="abs head" style="left:14px;top:14px;font-size:15px;display:flex;gap:6px;align-items:center"><span style="width:14px;height:14px;border:1.5px solid var(--gold);border-radius:3px"></span>Dashboard</div>
        <div class="side-item" style="top:78px"><i></i>Dashboard</div>
        <div class="abs" style="left:0;top:99px;width:127px;height:24px;background:#1d2c46;border-left:2px solid var(--gold)"></div>
        <div class="side-item" style="top:106px"><i></i>Production Analytics</div>
        <div class="side-item" style="top:134px"><i></i>Investment Tracker</div>
        <div class="side-item" style="top:162px"><i></i>Project Tracker</div>
        <div class="side-item" style="top:190px"><i></i>Mozambique Operations</div>
        <div class="side-item" style="top:218px"><i></i>Energy Procurement</div>
        <div class="side-item" style="top:246px"><i></i>Rota Africa</div>
        <div class="side-item" style="top:275px"><i></i>Capitalisation</div>
        <div class="side-item" style="top:303px"><i></i>Gathboard</div>
        <div class="side-item" style="top:331px"><i></i>Production</div>
        <div class="side-item" style="top:392px"><i></i>Pipeline Generation</div>
        <div class="side-item" style="top:420px"><i></i>Mozambique Codes</div>
      </div>
      <div class="abs head" style="left:141px;top:10px;font-size:11px;color:var(--gold)">Energy Production Overview</div>
      <div class="abs" style="left:141px;top:25px;font-size:7px;color:var(--muted)">Energy Map v2.1</div>
      <div class="abs head" style="left:141px;top:47px;font-size:11px;color:var(--gold)">Mozambique Energy Map v2.1</div>
      <div class="pill" style="left:648px;top:12px;width:64px;height:20px;border-radius:4px;font-size:7px">▢ Api Yield</div>
      <div class="pill" style="left:720px;top:12px;width:84px;height:20px;border-radius:4px;font-size:7px;background:var(--gold);color:#111;border:none">⌖ Extraction ⌄</div>
      <div class="pill" style="left:639px;top:44px;width:62px;height:15px;border-radius:4px;font-size:6px">Position ⌄</div>
      <div class="pill" style="left:707px;top:44px;width:55px;height:15px;border-radius:4px;font-size:6px">Forecast ⌄</div>
      <div class="pill" style="left:767px;top:44px;width:36px;height:15px;border-radius:4px;font-size:6px;color:var(--gold)">Gold</div>
      <div class="ph" style="left:141px;top:66px;width:320px;height:381px;background:radial-gradient(circle at 57% 62%,#a8884a 0,#5c5a4a 10%,#213353 26%,#1b2b47 60%)" role="img" aria-label="Map of Mozambique energy zones with pipelines and exploration blocks"></div>

      <div class="chart" style="left:470px;top:66px;width:162px;height:99px"><div class="t">Monthly Hydrocarbon Yield</div>
        <svg class="abs" style="left:8px;top:24px" width="146" height="64"><g stroke="#2c3e5c"><line x1="14" y1="8" x2="146" y2="8"/><line x1="14" y1="24" x2="146" y2="24"/><line x1="14" y1="40" x2="146" y2="40"/><line x1="14" y1="56" x2="146" y2="56"/></g><polyline points="18,46 38,34 56,18 76,36 96,30 118,34 138,8" fill="none" stroke="#e6ebf1" stroke-width="1.2"/><path d="M18 46L38 34L56 18L76 36L96 30L118 34L138 8V56H18Z" fill="#e4b53f" opacity=".25"/></svg></div>
      <div class="chart" style="left:641px;top:66px;width:162px;height:99px"><div class="t">Monthly Hydrocarbon Yield</div>
        <svg class="abs" style="left:8px;top:24px" width="146" height="64"><g stroke="#2c3e5c"><line x1="14" y1="8" x2="146" y2="8"/><line x1="14" y1="24" x2="146" y2="24"/><line x1="14" y1="40" x2="146" y2="40"/><line x1="14" y1="56" x2="146" y2="56"/></g><polyline points="18,44 36,34 58,40 78,26 98,34 118,20 140,12" fill="none" stroke="#e6ebf1" stroke-width="1.2"/><path d="M18 44L36 34L58 40L78 26L98 34L118 20L140 12V56H18Z" fill="#e4b53f" opacity=".25"/></svg></div>
      <div class="chart" style="left:470px;top:173px;width:162px;height:109px"><div class="t">Regional Investment Allocation</div>
        <svg class="abs" style="left:8px;top:26px" width="146" height="70"><g fill="#3a5a8c"><rect x="18" y="40" width="10" height="24"/><rect x="46" y="30" width="10" height="34"/><rect x="74" y="14" width="10" height="50"/><rect x="102" y="42" width="10" height="22"/><rect x="128" y="24" width="10" height="40"/></g><g fill="#e4b53f"><rect x="18" y="36" width="10" height="4"/><rect x="74" y="6" width="10" height="8"/><rect x="102" y="38" width="10" height="4"/><rect x="128" y="12" width="10" height="12"/></g></svg></div>
      <div class="chart" style="left:641px;top:173px;width:162px;height:109px"><div class="t">Regional Investment Allocation</div>
        <svg class="abs" style="left:8px;top:26px" width="146" height="70"><g fill="#3a5a8c"><rect x="18" y="38" width="10" height="26"/><rect x="46" y="28" width="10" height="36"/><rect x="74" y="20" width="10" height="44"/><rect x="102" y="36" width="10" height="28"/><rect x="128" y="40" width="10" height="24"/></g><g fill="#e4b53f"><rect x="18" y="34" width="10" height="4"/><rect x="46" y="18" width="10" height="10"/><rect x="74" y="8" width="10" height="12"/><rect x="102" y="30" width="10" height="6"/><rect x="128" y="30" width="10" height="10"/></g></svg></div>
      <div class="chart" style="left:470px;top:290px;width:333px;height:157px"><div class="t" style="font-size:9px;color:var(--gold)">Investment Tracking</div>
        <svg class="abs" style="left:8px;top:30px" width="160" height="90"><g stroke="#2c3e5c"><line x1="14" y1="6" x2="160" y2="6"/><line x1="14" y1="26" x2="160" y2="26"/><line x1="14" y1="46" x2="160" y2="46"/><line x1="14" y1="66" x2="160" y2="66"/><line x1="14" y1="86" x2="160" y2="86"/></g><rect x="36" y="54" width="16" height="32" fill="#3a5a8c"/><rect x="36" y="50" width="16" height="6" fill="#e4b53f"/><rect x="78" y="42" width="16" height="44" fill="#3a5a8c"/><rect x="78" y="38" width="16" height="6" fill="#e4b53f"/><rect x="116" y="20" width="16" height="66" fill="#e4b53f"/><rect x="116" y="14" width="16" height="8" fill="#fff"/></svg>
        <svg class="abs" style="left:198px;top:30px" width="92" height="92"><circle cx="46" cy="46" r="38" fill="none" stroke="#2c3e5c" stroke-width="9"/><circle cx="46" cy="46" r="38" fill="none" stroke="#e4b53f" stroke-width="9" stroke-dasharray="150 90" transform="rotate(-90 46 46)"/><circle cx="46" cy="46" r="38" fill="none" stroke="#fff" stroke-width="9" stroke-dasharray="40 199" stroke-dashoffset="-150" transform="rotate(-90 46 46)"/><text x="46" y="44" text-anchor="middle" font-size="7" fill="#dfe4ea">Portfolio</text><text x="46" y="53" text-anchor="middle" font-size="7" fill="#dfe4ea">Diversification</text></svg>
        <div class="abs" style="left:300px;top:34px;font-size:6px;line-height:2.6;color:#dfe4ea">■ $82%<br>■ $22%<br>■ $02%<br>■ $22%<br>■ $43%</div>
      </div>
      <div class="abs" style="left:470px;top:420px;width:333px;height:27px;border-top:1px solid var(--line);font-size:8px;display:flex;align-items:center;gap:8px;padding-left:10px;color:#dfe4ea;white-space:nowrap">Active Projects: <span style="color:var(--gold)">18</span> | Total CapEx: <span style="color:var(--gold)">$18.7B</span> | ROI Forecast: <span style="color:var(--gold)">14.2%</span></div>
    </div>
  </div>

  <div class="abs" style="left:0;top:905px;width:908px;height:1px;background:var(--line)"></div>

  <div class="abs label" style="left:24px;top:972px;font-size:7px">MARKET INTELLIGENCE</div>
  <h2 class="abs head" style="left:24px;top:986px;font-size:37px;white-space:nowrap">Industry Intelligence Feed</h2>
  <div class="pill" style="left:566px;top:996px;width:48px;height:24px;color:var(--gold);border-color:var(--gold-soft);background:#1b2230;font-size:8px">ALL</div>
  <div class="pill" style="left:622px;top:996px;width:80px;height:24px;font-size:8px">INVESTMENT</div>
  <div class="pill" style="left:710px;top:996px;width:88px;height:24px;font-size:8px">OPERATIONS</div>
  <div class="pill" style="left:797px;top:996px;width:85px;height:24px;font-size:8px">EXPLORATION</div>

  <article class="ncard" style="left:24px"><div class="img" style="background:linear-gradient(160deg,#5f8fc2,#2c6e9f 45%,#8a8f80)" role="img" aria-label="Coastal fjord landscape"></div><span class="ago">11m ago</span><div class="cat">INVESTMENT</div><h5>Veridane &amp; NHC Announce $1.2B Investment in Lumara LNG Phase 2</h5><p>Major milestone for Mozambique's natural gas ambitions as French major advances massive offshore project.</p><div class="meta"><span class="mono" style="color:var(--dim)">4 min READ</span><span style="color:var(--gold)">FULL STORY ›</span></div></article>
  <article class="ncard" style="left:316px"><div class="img" style="background:linear-gradient(160deg,#7bb2db,#4d7a45 50%,#c0404f)" role="img" aria-label="Red blossoms against a blue sky"></div><span class="ago">47m ago</span><div class="cat">OPERATIONS</div><h5>Mozambique's Marlin Sul FLNG Exceeds 3.5M Tonnes Production Milestone</h5><p>The floating LNG facility continues to outperform expectations in the Rovuma Basin.</p><div class="meta"><span class="mono" style="color:var(--dim)">6 min READ</span><span style="color:var(--gold)">FULL STORY ›</span></div></article>
  <article class="ncard" style="left:607px"><div class="img" style="background:linear-gradient(170deg,#e7dcc9,#c9a278 55%,#8a5a34)" role="img" aria-label="Laptop and glasses on a wooden desk"></div><span class="ago">2h ago</span><div class="cat">EXPLORATION</div><h5>New Exploration Licenses Awarded in the Angoche Basin</h5><p>NPA awards 4 new blocks to consortium including Kestrel Corp and local partners.</p><div class="meta"><span class="mono" style="color:var(--dim)">3 min READ</span><span style="color:var(--gold)">FULL STORY ›</span></div></article>
  <div class="pill" style="left:365px;top:1369px;width:178px;height:34px;border-radius:14px;border-color:#55637a;font-size:8px">BROWSE ENTIRE NEWS ARCHIVE →</div>

  <div class="abs" style="left:0;top:1470px;width:908px;height:310px;background:var(--black)"></div>
  <div class="abs" style="left:24px;top:1520px;width:858px;height:210px;border:1px solid #1e2836;border-radius:14px;background:#090d14">
    <div class="abs label" style="left:38px;top:38px;font-size:7px">BECOME A MEMBER TODAY</div>
    <h2 class="abs head" style="left:38px;top:58px;width:500px;font-size:37px">Ready to lead the next chapter of Mozambique's energy story?</h2>
    <p class="abs" style="left:38px;top:144px;width:200px;font-size:9px;line-height:1.6;color:#c7d0dc">Join over 1,800 verified industry participants already using Tarnovex.</p>
    <div class="abs btn-gold" style="left:588px;top:66px;width:232px;height:54px;border-radius:12px;font-size:11px;letter-spacing:.08em;gap:18px">START FREE TRIAL <span style="background:#c49a2e;border-radius:10px;padding:3px 10px;font-size:7px">14 DAYS</span></div>
    <div class="abs" style="left:588px;top:135px;width:232px;text-align:center;font-size:7px;color:var(--dim)">No credit card required • Cancel anytime</div>
  </div>

  <div class="abs" style="left:62px;top:1832px;width:66px;height:66px;border:2px solid var(--gold);border-radius:6px"></div>
  <div class="abs" style="left:46px;top:1908px;width:98px;text-align:center;font-family:Outfit,sans-serif;font-weight:500;font-size:11px;letter-spacing:.1em">TARNOVEX</div>
  <div class="abs" style="left:40px;top:1940px;width:110px;text-align:center;font-size:7px;font-weight:500;white-space:nowrap">MAPUTO • BEIRA • PEMBA</div>
  <div class="fcol" style="left:196px"><b>PLATFORM</b>Discover Projects<br>Investment Database<br>Live Map<br>Supplier Directory</div>
  <div class="fcol" style="left:368px"><b>COMPANY</b>About Us<br>Our Story<br>Careers at Tarnovex<br>Press<br>Contact</div>
  <div class="fcol" style="left:540px"><b>RESOURCES</b>Help Center<br>API Documentation<br>Regulatory Library<br>Energy Reports<br>Webinars</div>
  <div class="fcol" style="left:712px"><b>FOLLOW UPDATES</b></div>
  <div class="abs" style="left:712px;top:1852px;display:flex;gap:10px"><span style="width:20px;height:20px;border:1px solid var(--line);border-radius:50%"></span><span style="width:20px;height:20px;border:1px solid var(--line);border-radius:50%"></span><span style="width:20px;height:20px;border:1px solid var(--line);border-radius:50%"></span></div>
  <div class="abs mono" style="left:712px;top:1902px;font-size:5px;line-height:1.8;color:#a5b1bf">© TARNOVEX 2025<br>MOZAMBIQUE LDA</div>
  <div class="abs" style="left:0;top:2006px;width:908px;text-align:center;font-size:6px;letter-spacing:.08em;color:#3a4658">A PREMIUM EXPERIENCE FOR THE MOZAMBICAN OIL &amp; GAS ECOSYSTEM</div>
  <div class="abs" style="left:850px;top:1987px;width:38px;height:38px;border-radius:10px;background:var(--gold);display:flex;align-items:center;justify-content:center">
    <svg width="20" height="20" viewBox="0 0 20 20"><path d="M10 3a7 7 0 1 1-3.5 13L3 17l1-3.5A7 7 0 0 1 10 3z" fill="none" stroke="#111" stroke-width="1.6"/></svg>
  </div>
  <div class="abs" style="left:879px;top:1983px;width:12px;height:12px;border-radius:50%;background:var(--green);font-size:7px;color:#111;display:flex;align-items:center;justify-content:center">1</div>
</section>

</div>
</body>
</html>
```